I need a business card design for a new dance business. I offer classical Indian dance tuition and also professional performances. I want to offer the community a variety of Indian dance experiences which include: group class and private tuition, school and preschool educational courses and workshops. dance theatre performances, community function workshops and performances, Kids Bollywood parties, wedding & conference performances, mouth percussion classes, Indian mythology/ dance costume and make up workshops.
The final design should communicate a feeling and impression of the vibrance and energy of Indian dance.
Updates
Hi Everyone,
Project Deadline Extended
Reason: I would like to refine a few changes to the details of this lovely design and we have run out of time!
Project Deadline Extended
Reason: Still waiting to hear back form designer re two possible changes to the card design. Tomorrow is the deadline and I have sent several messages but with no response. I need to see this through before selecting this lovely design.
Thank you.
Tara
Industry/Entity Type
Preschool
Requirements
Must have
- The front of the business card should have the photo of me (my face and torso), surrounded entirely by a border of bright magenta (to match the magenta of my lipstick - it is the same as the magenta on my skirt in the second photo). Within the top border I want (perhaps yellow-gold) writing to say "Tara Holloway - Artistic Director" and within the bottom border it should read "Saffron Lantern Indian Dance." If you turn the card on its side the left border should have my telephone number: 0417 862 493 and the right-hand border should read: saffronlanternindiandance@quillmail.example
The reverse of the card should be the orange of the dance costume
and I'd like the picture of my feet and legs to be on the right side of the back of the card as a side border. Centre-aligned on the orange background it should read (perhaps in dark magenta):
Indian dance classes + private tuition
School + preschool educational courses and workshops
Dance theatre performances
Community function workshops and performances
Children's Bollywood parties
Wedding + conference performances
Mouth percussion classes
Indian mythology and dance demonstration workshops
Dance costume and make-up workshops
Nice to have
- A lovely artistic but easy-to-read font would be nice.

```html
<!DOCTYPE html>
<html lang="en">
<head>
<meta charset="utf-8">
<title>Saffron Lantern Indian Dance – Services Card</title>
<link rel="stylesheet" href="https://fonts.googleapis.com/css2?family=Jost:wght@400&display=swap">
<style>
  :root {
    --saffron: #f1b22b;
    --saffron-deep: #e7a222;
    --magenta-ink: #7d1f5c;
    --silk-magenta: #b0246f;
    --silk-orange: #e48a2a;
    --studio-grey: #bdb8b2;
  }
  html, body {
    margin: 0;
    padding: 0;
    width: 1200px;
    height: 899px;
    overflow: hidden;
    background: #ffffff;
  }
  .card {
    position: relative;
    width: 1200px;
    height: 899px;
    display: flex;
    overflow: hidden;
  }
  .services-panel {
    position: relative;
    width: 775px;
    height: 100%;
    background: var(--saffron);
  }
  .silhouette-pattern {
    position: absolute;
    inset: 0;
    background: radial-gradient(ellipse at 50% 45%, var(--saffron) 0%, var(--saffron) 55%, var(--saffron-deep) 100%);
  }
  .services-list {
    position: absolute;
    left: 0;
    right: 0;
    top: 193px;
    margin: 0;
    padding: 0;
    list-style: none;
    text-align: center;
    font-family: "Jost", "Futura", sans-serif;
    font-weight: 400;
    font-size: 26px;
    line-height: 57px;
    letter-spacing: 0.1px;
    color: var(--magenta-ink);
  }
  .dancer-photo {
    width: 425px;
    height: 100%;
    background:
      linear-gradient(100deg, transparent 0%, transparent 20%, rgba(176,36,111,0.95) 38%, var(--silk-magenta) 60%, var(--silk-orange) 78%, var(--studio-grey) 100%),
      var(--studio-grey);
  }
</style>
</head>
<body>
  <main class="card">
    <section class="services-panel">
      <div class="silhouette-pattern" role="img" aria-label="Repeating pattern of seated Indian dancer silhouettes in deeper saffron"></div>
      <ul class="services-list">
        <li>Indian dance classes + private tuition</li>
        <li>School + preschool educational courses and workshops</li>
        <li>Dance theatre performances</li>
        <li>Community function workshops and performances</li>
        <li>Children’s Bollywood parties</li>
        <li>Wedding + conference performances</li>
        <li>Mouth percussion classes</li>
        <li>Indian mythology and dance demonstration workshops</li>
        <li>Dance costume and make-up workshops</li>
      </ul>
    </section>
    <div class="dancer-photo" role="img" aria-label="Photograph of a classical Indian dancer's raised foot with ankle bells and a magenta and gold silk costume"></div>
  </main>
</body>
</html>
```